U.S. Popcorn company needs business cards

We are a popcorn company that manufactures popcorn and sells it to grocery stores worldwide. Our theme is "Americana" and our logo is U.S. route 66 which is the most famous highway in the U.S.

We would like the design to be simple and to use both sides. On the back side we would like to see just the logo and website. The front would be normal details

Target Market(s)

Wholesalers, grocers and distributors

Industry/Entity Type

Manufacture

Contact Information for Business Card

Business name: Prairie Lantern Popcorn
Phone: +1 555 308 4726
Email: Dale@prairielanternpopcorn.com
website: www.prairielanternpopcorn.com
Tag Line: "FRESH from the prairie"
Name: Dale Whitcombe
Title: Founder/President

Requirements
Must have
• Either this design should be fun or clean and simple. I will let you show me your thougths.
Nice to have
• Anything that ties in the real Hwy Route 66.
• Colors might need to be red, white and blue incorporated.
Should not have
• Not be too busy.

```html
<!DOCTYPE html>
<html lang="en">
<head>
<meta charset="utf-8">
<title>Prairie Lantern Popcorn – Business Cards</title>
<link href="https://fonts.googleapis.com/css2?family=Source+Sans+3:ital,wght@0,400;0,600;0,700;1,400;1,600&display=swap" rel="stylesheet">
<style>
  :root {
    --navy: #0a2a6c;
    --navy-deep: #05276a;
    --red: #e1232b;
    --white: #ffffff;
    --ink: #4a4a4a;
    --backdrop: #efeeea;
  }
  * { margin: 0; padding: 0; box-sizing: border-box; }
  html, body {
    width: 1200px; height: 987px; overflow: hidden;
    background: var(--backdrop);
    font-family: "Source Sans 3", "Myriad Pro", Arial, sans-serif;
  }
  .stage { position: relative; width: 1200px; height: 987px; }
  .card {
    position: absolute; left: 293px; width: 615px; height: 352px;
    box-shadow: 0 2px 5px rgba(0,0,0,.25);
  }
  .card--front { top: 130px; background: var(--white); }
  .card--back { top: 505px; background: var(--navy-deep); }

  .accent-bar {
    position: absolute; left: 0; top: 191px; width: 9px; height: 49px;
    background: var(--navy);
  }
  .person-name {
    position: absolute; left: 33px; top: 188px;
    font-size: 23px; font-weight: 600; color: var(--navy);
    letter-spacing: .2px; text-transform: uppercase;
  }
  .person-title {
    position: absolute; left: 33px; top: 216px;
    font-size: 17px; color: var(--red);
  }
  .contact-list { position: absolute; left: 38px; top: 252px; list-style: none; }
  .contact-list li {
    display: flex; align-items: center; height: 23.5px;
    font-size: 15px; color: var(--ink);
  }
  .contact-list svg { width: 15px; height: 15px; margin-right: 10px; fill: var(--navy); }

  .brand-name {
    position: absolute; display: flex; flex-direction: column;
    align-items: center; justify-content: center; text-align: center;
    font-weight: 700; text-transform: uppercase; line-height: 1.05;
  }
  .brand-name--front {
    left: 278px; top: 34px; width: 314px; height: 293px;
    color: var(--navy); font-size: 42px;
  }
  .brand-name--back {
    left: 205px; top: 80px; width: 205px; height: 192px;
    color: var(--white); font-size: 28px;
  }
  .brand-dot {
    width: 22px; height: 22px; border-radius: 50%;
    background: var(--red); margin-bottom: 14px;
  }
  .brand-name--back .brand-dot { background: var(--white); width: 16px; height: 16px; margin-bottom: 10px; }

  .tagline {
    position: absolute; left: 0; right: 0; top: 296px; text-align: center;
    color: var(--white); font-size: 17px; font-style: italic; font-weight: 600;
  }
  .tagline strong { font-style: normal; font-weight: 700; }
</style>
</head>
<body>
<main class="stage">
  <section class="card card--front" aria-label="Business card front">
    <div class="brand-name brand-name--front">
      <span class="brand-dot"></span>
      <span>Prairie</span><span>Lantern</span><span>Popcorn</span>
    </div>
    <div class="accent-bar"></div>
    <h1 class="person-name">Dale Whitcombe</h1>
    <p class="person-title">Founder/President</p>
    <ul class="contact-list">
      <li>
        <svg viewBox="0 0 16 16"><path d="M3.6 1.2l2.2 2.4c.4.4.4 1 0 1.4l-1 1.1a9 9 0 0 0 5.1 5.1l1.1-1c.4-.4 1-.4 1.4 0l2.4 2.2c.4.4.4 1 0 1.4l-1.3 1.2C11.6 16.8 0 5.4 1 2.5L2.2 1.2c.4-.4 1-.4 1.4 0z"/></svg>
        +1 555 308 4726
      </li>
      <li>
        <svg viewBox="0 0 16 16"><path d="M1 3h14v10H1z M1.5 3.5L8 9l6.5-5.5" fill="none" stroke="#0a2a6c" stroke-width="1.6"/></svg>
        Dale@prairielanternpopcorn.com
      </li>
      <li>
        <svg viewBox="0 0 16 16"><circle cx="8" cy="8" r="7"/><path d="M4 4.5c1.5.3 2 1.5 1.5 2.7-.4 1 .5 1.8 1.5 2 .8.2.8 1.5.2 2.6M10 2.5c-.5 1 .2 2 1.3 2.2 1 .2 1.6.9 1.6 1.8" fill="none" stroke="#fff" stroke-width="1.2"/></svg>
        www.prairielanternpopcorn.com
      </li>
    </ul>
  </section>

  <section class="card card--back" aria-label="Business card back">
    <div class="brand-name brand-name--back">
      <span class="brand-dot"></span>
      <span>Prairie</span><span>Lantern</span><span>Popcorn</span>
    </div>
    <p class="tagline"><strong>FRESH</strong> from the prairie</p>
  </section>
</main>
</body>
</html>
```